Harborline Auto LLC

Car Dealer Customer Service
Address: 2874 Cresthaven Road, Shelbyville, TN 37162
web: www.harborlineautoxq.net
email: harborlineautoxq@mailnest.example
Phone: (931) 555-0148
Phone: (629) 555-0173

```html
<!DOCTYPE html>
<html lang="en">
<head>
<meta charset="utf-8">
<title>Harborline Auto – Business Card</title>
<link href="https://fonts.googleapis.com/css2?family=Montserrat:wght@400;500;700;800&display=swap" rel="stylesheet">
<style>
  :root {
    --blue: #1f7fbf;
    --blue-deep: #136aa6;
    --blue-light: #2a9ad6;
    --yellow: #eab040;
    --yellow-deep: #e39f33;
    --paper: #f7f7f5;
    --ink: #555555;
    --stage: #1c1c1c;
  }
  * { box-sizing: border-box; margin: 0; padding: 0; }
  html, body {
    width: 1200px; height: 963px; overflow: hidden;
    background: var(--stage);
    font-family: "Montserrat", sans-serif;
  }
  .card {
    position: absolute; left: 250px; width: 700px; height: 400px;
    overflow: hidden; border-radius: 4px;
  }
  .card--front { top: 60px; background: var(--paper); }
  .card--back {
    top: 503px;
    background: linear-gradient(135deg, var(--yellow) 0%, var(--yellow-deep) 100%);
    display: flex; align-items: center; justify-content: center;
  }
  .card__waves { position: absolute; left: 0; top: 0; width: 700px; height: 400px; }

  .brand { display: flex; align-items: center; gap: 12px; }
  .brand__dot { width: 34px; height: 34px; border-radius: 50%; background: var(--blue); }
  .brand__name {
    font-weight: 800; color: var(--blue-deep); letter-spacing: 0.5px; font-size: 30px;
  }
  .card--front .brand { position: absolute; left: 70px; top: 48px; }
  .card--front .brand__dot { background: var(--yellow); }
  .card--back .brand__name { font-size: 44px; }
  .card--back .brand__dot { width: 46px; height: 46px; }

  .contact {
    position: absolute; left: 70px; top: 118px;
    color: var(--ink); font-size: 15px; line-height: 22px;
  }
  .contact__address { margin-bottom: 8px; }
  .contact__list { list-style: none; }
  .contact__item { display: flex; align-items: center; gap: 9px; }
  .contact__icon {
    width: 15px; height: 15px; border-radius: 50%; background: var(--yellow);
    display: inline-flex; align-items: center; justify-content: center; flex: none;
  }
  .contact__icon svg { width: 9px; height: 9px; }

  .person { position: absolute; right: 60px; top: 200px; text-align: right; }
  .person__name {
    font-weight: 700; color: var(--yellow); font-size: 22px; letter-spacing: 1.5px;
    text-transform: uppercase;
  }
  .person__role { color: var(--ink); font-size: 16px; margin-top: 2px; }
</style>
</head>
<body>

<section class="card card--front" aria-label="Business card front">
  <svg class="card__waves" viewBox="0 0 700 400" aria-hidden="true">
    <path d="M60,300 C250,350 480,345 700,255 L700,400 L0,400 L0,300 Z" fill="var(--yellow)"/>
    <path d="M40,268 C240,335 470,330 700,245 L700,262 C480,348 240,350 60,300 Z" fill="var(--blue-deep)"/>
    <path d="M70,272 C260,326 470,318 690,248 C470,326 260,338 80,290 Z" fill="var(--blue-light)"/>
    <path d="M60,300 C250,350 480,345 700,262 L700,268 C480,352 250,356 60,306 Z" fill="#ffffff"/>
  </svg>

  <div class="brand">
    <span class="brand__dot"></span>
    <span class="brand__name">HARBORLINE AUTO</span>
  </div>

  <div class="contact">
    <p class="contact__address">2874 Cresthaven Road<br>Shelbyville, TN 37162</p>
    <ul class="contact__list">
      <li class="contact__item">
        <span class="contact__icon"><svg viewBox="0 0 10 10"><path d="M2,1 L4,1 L4.5,3 L3.3,3.8 C3.9,5 5,6.1 6.2,6.7 L7,5.5 L9,6 L9,8 C5,8.5 1.5,5 2,1 Z" fill="#fff"/></svg></span>
        (931) 555-0148
      </li>
      <li class="contact__item">
        <span class="contact__icon"><svg viewBox="0 0 10 10"><path d="M2,1 L4,1 L4.5,3 L3.3,3.8 C3.9,5 5,6.1 6.2,6.7 L7,5.5 L9,6 L9,8 C5,8.5 1.5,5 2,1 Z" fill="#fff"/></svg></span>
        (629) 555-0173
      </li>
      <li class="contact__item">
        <span class="contact__icon"><svg viewBox="0 0 10 10"><rect x="1" y="2.5" width="8" height="5" fill="none" stroke="#fff" stroke-width="1"/><path d="M1,2.5 L5,5.5 L9,2.5" fill="none" stroke="#fff" stroke-width="1"/></svg></span>
        harborlineautoxq@mailnest.example
      </li>
      <li class="contact__item">
        <span class="contact__icon"><svg viewBox="0 0 10 10"><circle cx="5" cy="5" r="3.6" fill="none" stroke="#fff" stroke-width="1"/><path d="M1.4,5 L8.6,5 M5,1.4 C3.4,3.5 3.4,6.5 5,8.6 M5,1.4 C6.6,3.5 6.6,6.5 5,8.6" fill="none" stroke="#fff" stroke-width="0.8"/></svg></span>
        www.harborlineautoxq.net
      </li>
    </ul>
  </div>

  <div class="person">
    <p class="person__name">Marcus Delaney</p>
    <p class="person__role">Manager</p>
  </div>
</section>

<section class="card card--back" aria-label="Business card back">
  <div class="brand">
    <span class="brand__dot"></span>
    <span class="brand__name">HARBORLINE AUTO</span>
  </div>
</section>

</body>
</html>
```